Postcard design to acquire new clients for my Property Management Company

I'm looking for a postcard design that I can send to prospective clients detailing information about my company and services.
Postcard should be eye catching and contain information from www.bramblecrestpm.com. I've provided a few screen shots for the most important information and my logo.
Target Market(s)
Real Estate
Industry/Entity Type
Real Estate
Font styles to use
Sans Serif
Requirements
Must have
- Must be eye catching!! this will be a direct mail piece - I'd like for the card to be read and not tossed in the trash immediately.
Design que from the logo.
A place to write / print the receipts name and address.
our physical address - 2387 Hollow Pine Road, Lubbock, TX 79852.
Should not have
- the contact information on the business card is not accurate - please use info from website.

```html
<!DOCTYPE html>
<html lang="en">
<head>
<meta charset="UTF-8">
<title>Bramblecrest Property Management – Postcard</title>
<link href="https://fonts.googleapis.com/css2?family=Montserrat:wght@400;500;600;700&display=swap" rel="stylesheet">
<style>
  :root {
    --brand-navy: #0d4a80;
    --panel-blue: #084f87;
    --band-indigo: #29245f;
    --logo-bg: #f1f1f1;
    --accent-grey: #a7a7a9;
    --white: #ffffff;
    --icon-grey: #8a8a8c;
  }
  * { margin: 0; padding: 0; box-sizing: border-box; }
  html, body { width: 1200px; height: 816px; overflow: hidden; background: var(--white); }
  body { font-family: "Montserrat", sans-serif; }

  .postcard { position: relative; width: 1200px; height: 816px; background: var(--white); }

  .logo-box {
    position: absolute; left: 23px; top: 23px; width: 468px; height: 176px;
    background: var(--logo-bg);
    display: flex; flex-direction: column; align-items: center; justify-content: center;
    padding-top: 6px;
  }
  .logo-name {
    font-weight: 700; font-size: 35px; letter-spacing: 4px; color: var(--brand-navy); line-height: 1;
  }
  .logo-tagline {
    margin-top: 8px; font-weight: 500; font-size: 17.5px; letter-spacing: 3.2px; color: var(--brand-navy);
  }

  .services-panel {
    position: absolute; left: 23px; top: 199px; width: 468px; height: 456px;
    background: var(--panel-blue); color: var(--white);
    padding: 22px 0 0 36px; z-index: 2;
  }
  .services-title { font-weight: 700; font-size: 28px; line-height: 38px; }
  .services-lead { margin-top: 8px; font-weight: 600; font-size: 16.5px; line-height: 21px; }
  .services-list { list-style: none; margin-top: 12px; }
  .services-list li {
    position: relative; padding-left: 17px; font-weight: 500; font-size: 19px; line-height: 29.5px;
  }
  .services-list li::before {
    content: ""; position: absolute; left: 0; top: 12px; width: 8px; height: 8px;
    border-radius: 50%; background: var(--white);
  }

  .hero-photo {
    position: absolute; left: 491px; top: 23px; width: 687px; height: 487px;
    background: linear-gradient(180deg, #6d7a8e 0%, #9aa0aa 30%, #7b746c 55%, #c99a5e 72%, #6f6a5f 88%, #8a9466 100%);
  }

  .plans-band {
    position: absolute; left: 23px; top: 510px; width: 1155px; height: 232px;
    background: var(--band-indigo); color: var(--white);
  }
  .plans-title {
    position: absolute; left: 549px; top: 34px;
    font-weight: 700; font-size: 27.5px; line-height: 40px;
  }
  .plan-options { position: absolute; left: 549px; top: 122px; display: flex; }
  .plan { display: flex; align-items: flex-start; font-size: 14.5px; line-height: 18px; }
  .plan + .plan { margin-left: 22px; }
  .plan svg { margin: 2px 9px 0 0; flex: none; }
  .plan-name { font-weight: 500; }
  .plan-price { font-weight: 600; }

  .contact-strip {
    position: absolute; left: 23px; top: 742px; width: 1155px; height: 54px;
    display: flex; align-items: center; padding-left: 24px;
  }
  .contact-item {
    display: flex; align-items: center; font-weight: 500; font-size: 18.5px; color: var(--brand-navy);
  }
  .contact-item svg { margin-right: 17px; }
  .contact-item + .contact-item { margin-left: 22px; }

  .corner-shapes { position: absolute; left: 0; top: 0; }
</style>
</head>
<body>
<div class="postcard">

  <div class="logo-box">
    <div class="logo-name">BRAMBLECREST</div>
    <div class="logo-tagline">PROPERTY MANAGEMENT</div>
  </div>

  <div class="hero-photo" role="img" aria-label="Photo of a modern two-storey house with warm lit windows at dusk"></div>

  <div class="plans-band">
    <h2 class="plans-title">CHOOSE THE RIGHT PROPERTY<br>MANAGEMENT SYSTEM</h2>
    <div class="plan-options">
      <div class="plan">
        <svg width="13" height="11" viewBox="0 0 13 11"><polyline points="1,6 5,10 12,1" fill="none" stroke="#fff" stroke-width="1.8"/></svg>
        <div><div class="plan-name">LEASE ONLY</div><div class="plan-price">9% Annual Lease</div></div>
      </div>
      <div class="plan">
        <svg width="13" height="11" viewBox="0 0 13 11"><polyline points="1,6 5,10 12,1" fill="none" stroke="#fff" stroke-width="1.8"/></svg>
        <div><div class="plan-name">FULL SERVICE</div><div class="plan-price">10% of monthly rent</div></div>
      </div>
      <div class="plan">
        <svg width="13" height="11" viewBox="0 0 13 11"><polyline points="1,6 5,10 12,1" fill="none" stroke="#fff" stroke-width="1.8"/></svg>
        <div><div class="plan-name">PREMIUM SERVICE</div><div class="plan-price">12% of monthly rent</div></div>
      </div>
    </div>
  </div>

  <section class="services-panel">
    <h1 class="services-title">PROPERTY MANAGEMENT<br>ACROSS LUBBOCK, TX</h1>
    <p class="services-lead">Maximize your financial returns with<br>support from our rental specialists</p>
    <ul class="services-list">
      <li>Property Marketing</li>
      <li>Tenant Screening</li>
      <li>Rent Collection</li>
      <li>Maintenance</li>
      <li>Property Inspections</li>
      <li>Financial Reporting</li>
      <li>Evictions</li>
      <li>Legal Guidance</li>
    </ul>
  </section>

  <svg class="corner-shapes" width="1200" height="816" viewBox="0 0 1200 816">
    <polygon points="834,742 1178,742 1178,796 811,796" fill="var(--accent-grey)"/>
    <polygon points="751,742 834,742 811,796" fill="var(--band-indigo)"/>
  </svg>

  <div class="contact-strip">
    <div class="contact-item">
      <svg width="20" height="20" viewBox="0 0 20 20"><rect width="20" height="20" rx="5" fill="var(--icon-grey)"/><path d="M6.5 4.5c.6-.4 1.3-.2 1.6.4l.9 1.8c.3.5.1 1.1-.3 1.4l-.8.6c.6 1.4 1.6 2.5 3 3.2l.6-.8c.3-.4.9-.6 1.4-.3l1.8.9c.6.3.8 1 .4 1.6l-.6.9c-.5.7-1.4 1-2.2.7C9.1 14 6 10.9 4.9 7.8c-.3-.8 0-1.7.7-2.2z" fill="#fff"/></svg>
      (806) 555-0147
    </div>
    <div class="contact-item">
      <svg width="20" height="16" viewBox="0 0 20 16"><rect width="20" height="16" rx="3" fill="var(--icon-grey)"/><polyline points="3,4 10,9 17,4" fill="none" stroke="#fff" stroke-width="1.6"/></svg>
      info@bramblecrestpm.com
    </div>
  </div>

</div>
</body>
</html>
```